Vortel surface design based website for technology jobs website

We need a website design for a technology job listing website, mainly aiming at 20/30/40 year old nerds. Jobs listed from multiple sources will be concatenated and organised. This website will be built with Vortel surface design (https://surfacekit.example/guidelines/) so please use their components. The design should be simple and clear, so a user can directly look for offerings that are interesting for him.

Three different pages will be needed:

1. Main jobs list page

Contains a large table (https://surfacekit.example/guidelines/components/data-tables.html#data-tables-structure), on top or next to this data-table users should be able to apply filters (select countries, select salary ranges) and somewhere an overview of the selected filters should be shown.

- A subscribe bar should be shown somewhere to allow a user to register for weekly/monthly mailings for new job offers with his preferred search filters.

2. Selected item page

If an item is clicked, a user should be able to view a job posting and it's details.

3. An advertiser should be able post his job offer.
Similar fields as https://post.ledgerworkboard.example/.
(https://surfacekit.example/guidelines/components/text-fields.html#text-fields-layout)

Target Market(s)

20/30/40 year old nerds.

Industry/Entity Type

Computer

Logo Text

TechHirePlaza.example

Number of Pages Required

3 page

Colors

Designer to choose colors to be used in the design.

Requirements
Must have
• 1. Main jobs list page
• Contains a large table (https://surfacekit.example/guidelines/components/data-tables.html#data-tables-structure), on top or next to this data-table users should be able to apply filters (select countries, select salary ranges) and somewhere an overview of the selected filters should be shown.
• - A subscribe bar should be shown somewhere to allow a user to register for weekly/monthly mailings for new job offers with his preferred search filters.
• 2. Selected item page
• If an item is clicked, a user should be able to view a job posting and it's details.
• 3. An advertiser should be able post his job offer,
• (https://surfacekit.example/guidelines/components/text-fields.html#text-fields-layout)
• Please use open fonts!

```html
<!DOCTYPE html>
<html lang="en">
<head>
<meta charset="utf-8">
<title>Post a Job</title>
<link href="https://fonts.googleapis.com/css2?family=Roboto:wght@400;500;700&display=swap" rel="stylesheet">
<style>
  :root {
    --navy: #0b2d56;
    --navy-deep: #061a36;
    --sky: #05a9f0;
    --button-blue: #0d4f94;
    --accent-blue: #1565c0;
    --teal-icon: #2aa6c4;
    --page-bg: #eeeeee;
    --card-bg: #ffffff;
    --text-dark: #222222;
    --text-muted: #6b6b6b;
    --line: #8a8a8a;
    --placeholder: #c8c8c8;
    --fab-red: #e03a2f;
    --footer-bg: #333538;
  }
  * { box-sizing: border-box; margin: 0; padding: 0; }
  html, body { width: 1040px; height: 1200px; overflow: hidden; }
  body {
    position: relative;
    background: var(--page-bg);
    font-family: "Roboto", Arial, sans-serif;
    color: var(--text-dark);
  }
  .sidebar {
    position: absolute; left: 0; top: 0; width: 58px; height: 1200px;
    background: #ffffff;
    box-shadow: 1px 0 3px rgba(0,0,0,0.25);
    z-index: 3;
  }
  .sidebar svg {
    position: absolute; left: 20px; width: 18px; height: 18px;
    fill: var(--teal-icon);
  }
  .hero {
    position: absolute; left: 58px; top: 0; width: 982px; height: 344px;
    background: radial-gradient(circle at 80% 20%, #1a5fa8 0%, rgba(26,95,168,0) 45%),
                linear-gradient(135deg, var(--navy-deep) 0%, var(--navy) 55%, #124a86 100%);
  }
  .brand {
    position: absolute; left: 74px; top: 14px;
    font-size: 27px; font-weight: 500; color: #ffffff;
  }
  .search-bar {
    position: absolute; left: 74px; top: 91px; width: 892px; height: 84px;
    background: var(--sky);
  }
  .search-field {
    position: absolute; top: 25px; height: 35px;
    background: #ffffff; border-radius: 2px;
    font-size: 11px; color: #8c8c8c;
    padding-left: 6px; line-height: 35px;
  }
  .search-field.filled { color: #555555; }
  .search-field svg {
    position: absolute; right: 7px; top: 14px; width: 8px; height: 6px;
    stroke: #777777; fill: none; stroke-width: 1.3;
  }
  .search-button {
    position: absolute; left: 779px; top: 25px; width: 87px; height: 35px;
    background: var(--button-blue); border-radius: 2px;
  }
  .search-button svg { position: absolute; left: 35px; top: 9px; width: 17px; height: 17px; }
  .form-card {
    position: absolute; left: 74px; top: 232px; width: 892px; height: 894px;
    background: var(--card-bg);
    box-shadow: 0 1px 3px rgba(0,0,0,0.2);
  }
  .section-title { position: absolute; left: 160px; font-size: 16px; font-weight: 400; color: var(--text-dark); }
  .field { position: absolute; left: 160px; width: 572px; border-bottom: 1px solid var(--line); }
  .field.narrow { width: 324px; }
  .field.active { border-bottom: 2px solid var(--accent-blue); }
  .field-label { position: absolute; left: 160px; font-size: 10px; color: #555555; }
  .field-label.active { color: var(--accent-blue); font-size: 9px; font-weight: 500; }
  .caret { position: absolute; left: 160px; top: 92px; width: 1px; height: 14px; background: #555; }
  .logo-drop {
    position: absolute; left: 508px; top: 384px; width: 223px; height: 110px;
    border: 1px solid #dddddd;
  }
  .logo-drop svg, .photo-drop svg { position: absolute; width: 36px; height: 32px; }
  .logo-drop svg { left: 94px; top: 30px; }
  .photo-drop {
    position: absolute; left: 159px; top: 643px; width: 78px; height: 78px;
    border: 1px solid #aaaaaa; border-radius: 50%;
  }
  .photo-drop svg { left: 21px; top: 20px; }
  .side-label { position: absolute; font-size: 10px; color: var(--text-muted); }
  .post-button {
    position: absolute; left: 160px; top: 821px; width: 143px; height: 33px;
    background: var(--sky); color: #ffffff; border-radius: 2px;
    font-size: 11px; font-weight: 500; text-align: center; line-height: 33px;
  }
  .fab {
    position: absolute; left: 976px; top: 1075px; width: 52px; height: 52px;
    border-radius: 50%; background: var(--fab-red);
    box-shadow: 0 2px 4px rgba(0,0,0,0.3);
  }
  .fab svg { position: absolute; left: 16px; top: 16px; width: 20px; height: 20px; }
  .footer {
    position: absolute; left: 58px; top: 1165px; width: 982px; height: 35px;
    background: var(--footer-bg); color: #ffffff;
    font-size: 10px; text-align: center; line-height: 35px;
  }
</style>
</head>
<body>
  <nav class="sidebar">
    <svg style="top:89px" viewBox="0 0 24 24"><path d="M12 3 1 12h3v9h6v-6h4v6h6v-9h3z"/></svg>
    <svg style="top:149px" viewBox="0 0 24 24"><path d="M2 21h20v2H2zM4 11h3v9H4zM9 6h3v14H9zM14 9h3v11h-3zM19 4h3v16h-3zM2 2h2v19H2z"/></svg>
    <svg style="top:210px" viewBox="0 0 24 24"><circle cx="12" cy="7" r="5"/><path d="M2 23c0-6 4-9 10-9s10 3 10 9z"/></svg>
    <svg style="top:271px" viewBox="0 0 24 24"><path d="M3 5h10v2H5v12h12v-8h2v10H3z"/><path d="M18 2l4 4-10 10H8v-4z"/></svg>
    <svg style="top:332px" viewBox="0 0 24 24"><path d="M2 2h16l4 4v16H2zm4 2v6h10V4zm6 1h2v4h-2zM5 13v7h14v-7z"/></svg>
    <svg style="top:393px" viewBox="0 0 24 24"><path d="M6 10V7a6 6 0 0 1 12 0v3h2v13H4V10zm3 0h6V7a3 3 0 0 0-6 0z"/></svg>
  </nav>

  <header class="hero" role="img" aria-label="Dark blue abstract technology background"></header>
  <div class="brand">Logo Name</div>

  <div class="search-bar">
    <div class="search-field" style="left:26px;width:253px">Keyword e.g. ( jobTitle, Description,Tags)<svg viewBox="0 0 8 6"><path d="M1 1l3 3 3-3"/></svg></div>
    <div class="search-field" style="left:287px;width:185px">Select Location<svg viewBox="0 0 8 6"><path d="M1 1l3 3 3-3"/></svg></div>
    <div class="search-field filled" style="left:480px;width:185px">Salary<svg viewBox="0 0 8 6"><path d="M1 1l3 3 3-3"/></svg></div>
    <div class="search-field filled" style="left:673px;width:98px">Designation<svg viewBox="0 0 8 6"><path d="M1 1l3 3 3-3"/></svg></div>
    <div class="search-button"><svg viewBox="0 0 24 24" fill="none" stroke="#ffffff" stroke-width="3.2"><circle cx="10" cy="10" r="7"/><path d="M15 15l6 6"/></svg></div>
  </div>

  <main class="form-card">
    <h2 class="section-title" style="top:40px">Job Details</h2>
    <div class="field-label active" style="top:74px">Title &nbsp;*</div>
    <div class="caret"></div>
    <div class="field active" style="top:110px"></div>

    <div class="field-label" style="top:147px">Location</div>
    <div class="field" style="top:166px"></div>
    <div class="field-label" style="top:201px">City</div>
    <div class="field" style="top:220px"></div>
    <div class="field-label" style="top:256px">Description</div>
    <div class="field" style="top:313px"></div>

    <h2 class="section-title" style="top:346px;left:162px">Your Company Details?</h2>
    <div class="field-label" style="top:383px">Company Name</div>
    <div class="field narrow" style="top:401px"></div>
    <div class="field-label" style="top:437px">Website</div>
    <div class="field narrow" style="top:455px"></div>
    <div class="field-label" style="top:492px">Twitter</div>
    <div class="field narrow" style="top:511px"></div>

    <div class="logo-drop"><svg viewBox="0 0 36 32"><circle cx="18" cy="3" r="2.5" fill="var(--placeholder)"/><path d="M12 8l6-4 6 4" stroke="var(--placeholder)" fill="none" stroke-width="1.2"/><rect x="2" y="9" width="32" height="22" fill="var(--placeholder)"/><rect x="5" y="12" width="26" height="16" fill="#ffffff"/><path d="M6 27l8-8 5 5 4-3 7 6z" fill="var(--placeholder)"/><circle cx="12" cy="16" r="2" fill="var(--placeholder)"/></svg></div>
    <div class="side-label" style="left:508px;top:501px;font-size:11px">Logo</div>

    <h2 class="section-title" style="top:545px">Let's get personal</h2>
    <div class="field-label" style="top:583px">Your or Your Boss Name</div>
    <div class="field" style="top:601px"></div>

    <div class="photo-drop"><svg viewBox="0 0 36 32"><circle cx="18" cy="3" r="2.5" fill="var(--placeholder)"/><path d="M12 8l6-4 6 4" stroke="var(--placeholder)" fill="none" stroke-width="1.2"/><rect x="2" y="9" width="32" height="22" fill="var(--placeholder)"/><rect x="5" y="12" width="26" height="16" fill="#ffffff"/><path d="M6 27l8-8 5 5 4-3 7 6z" fill="var(--placeholder)"/><circle cx="12" cy="16" r="2" fill="var(--placeholder)"/></svg></div>
    <div class="side-label" style="left:255px;top:676px;font-size:11px;color:#888">Photo</div>

    <div class="field-label" style="top:761px">Send application to</div>
    <div class="field" style="top:780px"></div>

    <div class="post-button">Post Your Job</div>
  </main>

  <div class="fab"><svg viewBox="0 0 20 20" stroke="#ffffff" stroke-width="2"><path d="M10 1v18M1 10h18"/></svg></div>

  <footer class="footer">Copyright © website address I All Rights Reaserved</footer>
</body>
</html>
```